Business Card Design Project

Looking to update our business cards. We have a logo with our slogan. We are an IT firm so we wouldlike a modern look.

Industry/Entity Type

Business

```html
<!DOCTYPE html>
<html lang="en">
<head>
<meta charset="utf-8">
<title>Lumenix Business Card</title>
<link rel="stylesheet" href="https://fonts.googleapis.com/css2?family=Open+Sans:wght@400;600&display=swap">
<style>
  :root {
    --backdrop: #e4e5e4;
    --paper: #f0f0ef;
    --forest: #435f32;
    --forest-deep: #3d5a2e;
    --lime: #8cc63f;
    --ink-light: #ffffff;
    --ink-muted: #dfe8d6;
  }
  * { box-sizing: border-box; margin: 0; padding: 0; }
  html, body {
    width: 1200px; height: 955px; overflow: hidden;
    background: var(--backdrop);
    font-family: "Open Sans", Arial, sans-serif;
  }
  .canvas {
    position: relative; width: 1200px; height: 955px;
  }
  .card {
    position: absolute; top: 334px;
    width: 500px; height: 286px;
    box-shadow: 0 10px 28px rgba(0,0,0,0.12);
    overflow: hidden;
  }
  .card--front { left: 70px; background: var(--paper); }
  .card--back { left: 630px; background: var(--forest); }

  /* Front */
  .front-band {
    position: absolute; left: 0; right: 0; bottom: 0; height: 150px;
    background: var(--forest);
    border-top: 4px solid var(--lime);
  }
  .front-band__split {
    position: absolute; left: 250px; top: 0; bottom: 0; width: 1px;
    background: var(--forest-deep);
  }
  .brand {
    position: absolute; left: 0; right: 0; top: 38px;
    text-align: center; color: var(--forest);
  }
  .brand__name {
    display: inline-flex; align-items: center; gap: 10px;
    font-size: 34px; font-weight: 600; letter-spacing: 5px;
  }
  .brand__dot {
    width: 14px; height: 14px; border-radius: 50%; background: var(--lime);
  }
  .brand__tagline {
    margin-top: 6px; font-size: 10px; font-weight: 600;
    letter-spacing: 3px; text-transform: uppercase;
  }
  .holder {
    position: absolute; left: 30px; bottom: 26px; color: var(--ink-light);
  }
  .holder__marker {
    position: absolute; left: -30px; top: 10px;
    width: 0; height: 0;
    border-top: 6px solid transparent; border-bottom: 6px solid transparent;
    border-left: 9px solid #1c2a14;
  }
  .holder__name { font-size: 17px; font-weight: 600; }
  .holder__role { font-size: 9px; color: #1c2a14; font-weight: 600; }
  .contact {
    position: absolute; right: 22px; top: 22px;
    text-align: right; color: var(--ink-light); font-size: 9.5px; line-height: 1.45;
  }
  .contact__address { margin-bottom: 8px; }
  .contact__line { display: flex; justify-content: flex-end; align-items: center; gap: 7px; }
  .contact__icon {
    width: 8px; height: 8px; background: var(--lime); border-radius: 1px;
  }

  /* Back */
  .back-mark {
    position: absolute; left: 0; right: 0; top: 50%;
    transform: translateY(-50%);
    display: flex; flex-direction: column; align-items: center; gap: 14px;
  }
  .back-mark__circle {
    width: 64px; height: 64px; border-radius: 50%; background: var(--lime);
  }
  .back-mark__name {
    color: var(--lime); font-size: 20px; font-weight: 600; letter-spacing: 4px;
  }
</style>
</head>
<body>
<main class="canvas">
  <section class="card card--front" aria-label="Business card front">
    <div class="brand">
      <div class="brand__name"><span>LUMENIX</span><span class="brand__dot"></span></div>
      <div class="brand__tagline">Technology Made Easy</div>
    </div>
    <div class="front-band">
      <div class="front-band__split"></div>
      <div class="holder">
        <span class="holder__marker"></span>
        <div class="holder__name">Daniel Moore</div>
        <div class="holder__role">Founder</div>
      </div>
      <div class="contact">
        <div class="contact__address">420 Maple Ridge Blvd<br>Suite 210<br>Fairview, OH 44126</div>
        <div class="contact__line"><span>123.555.0142</span><span class="contact__icon"></span></div>
        <div class="contact__line"><span>hello@lumenix.com</span><span class="contact__icon"></span></div>
        <div class="contact__line"><span>www.lumenix.com</span><span class="contact__icon"></span></div>
      </div>
    </div>
  </section>

  <section class="card card--back" aria-label="Business card back">
    <div class="back-mark">
      <span class="back-mark__circle"></span>
      <span class="back-mark__name">LUMENIX</span>
    </div>
  </section>
</main>
</body>
</html>
```